Brand new letterhead, business card, email signature etc.

We are a financial company in London, UK. Our website is www.marlowvane.com. We're wanting a complete remodel of the company colours, letter head, business cards, email signatures, etc. Looking to keep the same font for the company name. I have upload a colour palette that we want to work with. We're looking for company letterhead for outgoing letters/ correspondence, letterhead for internal documentation, email signatures, e-letters. etc. Ultimately we will redesign the entire website also. It is important that our clients get a strong, secure, warm, trustworthy, solid feeling and first impression.
Updates

Designs look the same

Target Market(s)

Institutional investors, (ultra) high net worth individuals

Industry/Entity Type

Finance, Invesments banking.

Font styles to use
Other font styles liked:
• Current font is "Champagne & Limousines"

Requirements
Must have
• Must use the colours provided on the PDF uploaded to the portal. The purple = main colour. The red = accent colour.
Nice to have
• Nice to use same font as now for the company name "Corvane". Font is "Champagne & Limousines". Nice to have some reference to the old logo flower, but only subtle.
Should not have
• Do not use the colour red from our website. Use the colours provided on the colour palette PDF that I uploaded in the portal.

```html
<!DOCTYPE html>
<html lang="en">
<head>
<meta charset="utf-8">
<title>Corvane — Business Card</title>
<link rel="stylesheet" href="https://fonts.googleapis.com/css2?family=Quicksand:wght@300;500;700&family=Montserrat:wght@700&display=swap">
<style>
  :root {
    --backdrop: #2a2433;
    --card: #1a1a1c;
    --brand-purple: #4a3a5e;
    --accent: #e0301e;
    --ink: #ffffff;
    --ink-soft: #e8e8e8;
  }
  * { margin: 0; padding: 0; box-sizing: border-box; }
  html, body { width: 1200px; height: 780px; overflow: hidden; }
  body {
    background: var(--backdrop);
    font-family: "Quicksand", sans-serif;
    display: flex;
    flex-direction: column;
    align-items: center;
    justify-content: center;
    gap: 30px;
  }
  .card {
    position: relative;
    width: 600px;
    height: 343px;
    background: var(--card);
    overflow: hidden;
  }
  .card__edge {
    position: absolute;
    left: 0; right: 0; bottom: 0;
    height: 4px;
    background: var(--accent);
  }

  /* Brand lockup */
  .brand {
    display: flex;
    align-items: center;
    color: var(--brand-purple);
    white-space: nowrap;
  }
  .brand__mark {
    border: 2px solid var(--brand-purple);
    flex: none;
  }
  .brand__name {
    font-family: "Quicksand", sans-serif;
    font-weight: 300;
    letter-spacing: 0.12em;
    text-transform: uppercase;
    line-height: 1;
  }

  /* Front */
  .card--front .brand {
    position: absolute;
    left: 88px;
    top: 120px;
    gap: 22px;
  }
  .card--front .brand__mark { width: 96px; height: 96px; }
  .card--front .brand__name { font-size: 66px; }

  /* Back: lockup runs upward along the left edge */
  .card--back .brand {
    position: absolute;
    left: 20px;
    bottom: 20px;
    height: 64px;
    gap: 18px;
    transform-origin: left bottom;
    transform: rotate(-90deg) translate(0, 64px);
  }
  .card--back .brand__mark { width: 64px; height: 64px; }
  .card--back .brand__name { font-size: 36px; }

  .contact {
    position: absolute;
    right: 54px;
    top: 40px;
    text-align: right;
    color: var(--ink-soft);
  }
  .contact__name {
    font-family: "Montserrat", sans-serif;
    font-weight: 700;
    font-size: 27px;
    color: var(--ink);
    line-height: 1.1;
  }
  .contact__first { color: var(--accent); }
  .contact__role {
    font-size: 14px;
    font-weight: 500;
    margin-top: 2px;
  }
  .contact__address {
    font-size: 13px;
    font-weight: 500;
    margin-top: 16px;
    line-height: 1.45;
  }
  .contact__lines {
    list-style: none;
    margin-top: 14px;
    font-size: 13px;
    font-weight: 500;
    line-height: 1.55;
  }
  .contact__lines li {
    display: flex;
    justify-content: flex-end;
    align-items: center;
    gap: 8px;
  }
  .contact__icon { width: 12px; height: 12px; flex: none; }
  .card__tab {
    position: absolute;
    right: 0;
    top: 40px;
    width: 18px;
    height: 58px;
    background: var(--accent);
  }
</style>
</head>
<body>

  <section class="card card--front" aria-label="Card front">
    <div class="brand">
      <span class="brand__mark"></span>
      <span class="brand__name">Corvane</span>
    </div>
    <span class="card__edge"></span>
  </section>

  <section class="card card--back" aria-label="Card back">
    <div class="brand">
      <span class="brand__mark"></span>
      <span class="brand__name">Corvane</span>
    </div>

    <span class="card__tab"></span>

    <div class="contact">
      <p class="contact__name"><span class="contact__first">Helena</span> Marsh</p>
      <p class="contact__role">Managing Director</p>
      <p class="contact__address">14 Aldergate Row, Floor 3<br>London EC2V 7HN</p>
      <ul class="contact__lines">
        <li>+44 20 7946 0318
          <svg class="contact__icon" viewBox="0 0 24 24" aria-hidden="true"><path fill="#e0301e" d="M6.6 10.8a15 15 0 0 0 6.6 6.6l2.2-2.2c.3-.3.7-.4 1-.2 1.1.4 2.3.6 3.6.6.6 0 1 .4 1 1V20c0 .6-.4 1-1 1A17 17 0 0 1 3 4c0-.6.4-1 1-1h3.5c.6 0 1 .4 1 1 0 1.3.2 2.5.6 3.6.1.3 0 .7-.2 1z"/></svg>
        </li>
        <li>info@marlowvane.com
          <svg class="contact__icon" viewBox="0 0 24 24" aria-hidden="true"><rect x="2" y="5" width="20" height="14" rx="2" fill="#e0301e"/><path d="M3 6l9 7 9-7" fill="none" stroke="#1a1a1c" stroke-width="2"/></svg>
        </li>
        <li>www.marlowvane.com
          <svg class="contact__icon" viewBox="0 0 24 24" aria-hidden="true"><circle cx="12" cy="12" r="10" fill="#e0301e"/><path d="M2 12h20M12 2c3 3 3 17 0 20M12 2c-3 3-3 17 0 20" fill="none" stroke="#1a1a1c" stroke-width="1.5"/></svg>
        </li>
      </ul>
    </div>

    <span class="card__edge"></span>
  </section>

</body>
</html>
```